Global (re)insurance broker needs a business card design

We need a classic business card for our company that is headquartered in SG, with offices in Malaysia and Dubai. We specialise in insurance and reinsurance broking and consultancy for our global clients.

```html
<!DOCTYPE html>
<html lang="en">
<head>
<meta charset="utf-8">
<title>Norvane business card</title>
<link href="https://fonts.googleapis.com/css2?family=Open+Sans:wght@400;600;700;800&display=swap" rel="stylesheet">
<style>
  :root {
    --backdrop: #2b2b2e;
    --card: #1d1d22;
    --card-deep: #16161a;
    --brand-blue: #2d4ca6;
    --brand-mint: #c7e0bd;
    --ink-light: #e4e4e6;
    --emboss: #141418;
  }
  * { margin: 0; padding: 0; box-sizing: border-box; }
  html, body {
    width: 1200px; height: 780px; overflow: hidden;
    background: var(--backdrop);
    font-family: "Open Sans", Arial, sans-serif;
  }
  .canvas {
    position: relative; width: 1200px; height: 780px;
    display: flex; align-items: center; justify-content: center; gap: 40px;
  }
  .card {
    position: relative; width: 540px; height: 310px;
    background: var(--card); overflow: hidden;
    box-shadow: 0 10px 30px rgba(0,0,0,0.35);
  }
  .wordmark {
    font-family: "Open Sans", Arial, sans-serif;
    font-weight: 800; color: var(--brand-mint);
    letter-spacing: 0.04em; line-height: 1;
  }
  .card-front .wordmark {
    position: absolute; left: 50%; top: 50%;
    transform: translate(-50%, -50%);
    font-size: 78px;
  }
  .emboss-mark {
    position: absolute; left: -6px; top: -14px;
    font-weight: 800; font-size: 92px; line-height: 1;
    letter-spacing: 0.04em; color: var(--emboss);
  }
  .card-back .wordmark {
    position: absolute; right: 44px; top: 86px;
    font-size: 46px;
  }
  .contact-block {
    position: absolute; right: 44px; top: 150px;
    text-align: right; color: var(--ink-light);
  }
  .person-name {
    font-weight: 600; font-size: 26px; color: var(--brand-blue); line-height: 1.1;
  }
  .person-role { font-size: 12.5px; margin-top: 2px; }
  .address { font-size: 11px; line-height: 1.35; margin-top: 8px; }
  .contact-list { list-style: none; margin-top: 8px; font-size: 11.5px; line-height: 1.55; }
  .contact-list li { display: flex; align-items: center; justify-content: flex-end; gap: 8px; }
  .contact-list svg { width: 12px; height: 12px; flex: none; }
  .accent-bar {
    position: absolute; right: 0; top: 150px; width: 22px; height: 64px;
    background: var(--brand-mint);
  }
</style>
</head>
<body>
<main class="canvas">
  <section class="card card-back" aria-label="Card back with contact details">
    <div class="emboss-mark" aria-hidden="true">NORVANE</div>
    <div class="wordmark">NORVANE</div>
    <div class="accent-bar"></div>
    <div class="contact-block">
      <p class="person-name">Mira Holt</p>
      <p class="person-role">Chief Operating Officer</p>
      <p class="address">22 Harbour Lane, Meridian<br>Tower #08-04, Singapore 048521</p>
      <ul class="contact-list">
        <li>+65 9000 1234
          <svg viewBox="0 0 12 12" aria-hidden="true"><rect x="3" y="0.8" width="6" height="10.4" rx="1" fill="none" stroke="var(--brand-mint)" stroke-width="1.2"/></svg>
        </li>
        <li>www.norvane.com
          <svg viewBox="0 0 12 12" aria-hidden="true"><circle cx="6" cy="6" r="5.4" fill="var(--brand-blue)"/><path d="M0.8 6h10.4M6 0.8c-2.4 2.8-2.4 7.6 0 10.4M6 0.8c2.4 2.8 2.4 7.6 0 10.4" fill="none" stroke="var(--card)" stroke-width="0.8"/></svg>
        </li>
        <li>mira@norvane.com
          <svg viewBox="0 0 12 12" aria-hidden="true"><rect x="0.8" y="2.5" width="10.4" height="7.5" fill="var(--brand-mint)"/><path d="M0.8 2.5 6 7l5.2-4.5" fill="none" stroke="var(--card)" stroke-width="1"/></svg>
        </li>
      </ul>
    </div>
  </section>

  <section class="card card-front" aria-label="Card front">
    <div class="wordmark">NORVANE</div>
  </section>
</main>
</body>
</html>
```